Natural healthcare clinic needs stationery and business card design

We have had a logo developed by Pixel Harbor and are now looking at utilising it for a new business concept. The concept is a natural healthcare clinic that hosts a number of small businesses. The individual practitioners may want to utilise the host business stationery to provide a consistent message to clients.

I am looking for a stationery design - letterhead, DL brochure template and business card that uses our logo. The business name 'Bright Meadows' is all about getting rhythm back into your life so you can be fit and healthy. The stationery design should reflect this.

There are a couple of requirements for the business card, it needs to be double-sided with black and white back. There should be lines to write appointment times on. The cards may need to be custom named on the front for example Carol Fenwick, Remedial Therapist and Aromatherapist. Therefore if a template can be provided so we can customise this information using MS Publisher, it would be appreciated.

The DL brochure template needs to be A4 folded to DL. I am looking for a consistent brand message that can be utilised to produce our own clinic brochures.

The natural healthcare clinic will host the following types of businesses - remedial massage, pregnancy massage, oncology massage, aromatherapy, acupuncture - as a bit of a guide.

Target Market(s)

25-45 year old male and females who work full time.

Industry/Entity Type

Healthcare

Requirements
Must have
• Use the logo I have already.

```html
<!DOCTYPE html>
<html lang="en">
<head>
<meta charset="utf-8">
<title>Bright Meadows — Business Card</title>
<link href="https://fonts.googleapis.com/css2?family=Open+Sans:wght@400;600&display=swap" rel="stylesheet">
<style>
  :root {
    --canvas: #ece8e1;
    --card-white: #ffffff;
    --green-light: #a6c93a;
    --green-dark: #6f9a1e;
    --peach: #f7c4a0;
    --ink-grey: #5b5b4e;
    --olive: #8a9a3a;
    --black: #0b0b0b;
    --text-white: #ffffff;
    --accent-orange: #f08a1c;
  }
  * { margin: 0; padding: 0; box-sizing: border-box; }
  html, body { width: 1200px; height: 1024px; overflow: hidden; }
  body {
    background: var(--canvas);
    font-family: "Open Sans", Arial, sans-serif;
    position: relative;
  }
  .card {
    position: absolute;
    left: 180px;
    width: 840px;
    height: 480px;
    overflow: hidden;
    box-shadow: 0 6px 18px rgba(0,0,0,0.18);
  }
  .card-front { top: 24px; background: var(--card-white); }
  .card-back { top: 520px; background: var(--black); }

  .front-shape { position: absolute; inset: 0; }

  .brand {
    position: absolute;
    display: flex;
    align-items: center;
    gap: 14px;
    font-weight: 400;
    white-space: nowrap;
  }
  .brand-dot { border-radius: 50%; flex: none; }
  .card-front .brand { left: 70px; top: 150px; font-size: 46px; color: var(--ink-grey); }
  .card-front .brand-dot { width: 30px; height: 30px; background: var(--green-light); }

  .contact-list {
    position: absolute;
    right: 50px;
    top: 56px;
    list-style: none;
    color: var(--text-white);
    font-size: 19px;
    line-height: 30px;
  }
  .contact-list li { display: flex; align-items: center; gap: 12px; }
  .contact-icon { width: 16px; height: 16px; flex: none; }

  .holder {
    position: absolute;
    left: 60px;
    bottom: 48px;
    color: var(--text-white);
  }
  .holder-name { font-size: 26px; font-weight: 600; }
  .holder-title { font-size: 18px; font-weight: 400; }
  .holder-address { font-size: 18px; line-height: 25px; margin-top: 8px; }

  .card-back .brand {
    left: 50%;
    top: 190px;
    transform: translateX(-50%);
    font-size: 54px;
    color: var(--olive);
  }
  .card-back .brand-dot { width: 34px; height: 34px; background: var(--green-light); }
  .back-web {
    position: absolute;
    left: 0; right: 0;
    top: 290px;
    text-align: center;
    color: var(--olive);
    font-size: 20px;
    letter-spacing: 0.5px;
  }
</style>
</head>
<body>
  <section class="card card-front" aria-label="Business card front">
    <svg class="front-shape" viewBox="0 0 840 480" width="840" height="480" aria-hidden="true">
      <defs>
        <linearGradient id="greenBand" x1="0" y1="1" x2="1" y2="0">
          <stop offset="0" stop-color="var(--green-dark)"/>
          <stop offset="0.5" stop-color="var(--green-light)"/>
          <stop offset="1" stop-color="var(--green-dark)"/>
        </linearGradient>
      </defs>
      <path d="M505 0 C600 150 420 300 0 310 L0 480 L840 480 L840 0 Z" fill="var(--peach)"/>
      <path d="M530 0 C630 160 450 320 0 332 L0 480 L840 480 L840 0 Z" fill="url(#greenBand)"/>
    </svg>

    <div class="brand"><span class="brand-dot"></span>Bright Meadows</div>

    <ul class="contact-list">
      <li><svg class="contact-icon" viewBox="0 0 16 16"><path d="M3 1 L6 1 L7 5 L5 6 C6 8.5 7.5 10 10 11 L11 9 L15 10 L15 13 C15 14 14 15 13 15 C7 15 1 9 1 3 C1 2 2 1 3 1 Z" fill="var(--accent-orange)"/></svg>555-210-4471</li>
      <li><svg class="contact-icon" viewBox="0 0 16 16"><rect x="3" y="1" width="10" height="14" rx="2" fill="var(--accent-orange)"/><rect x="5" y="3" width="6" height="8" fill="var(--green-light)"/></svg>555-308-2296</li>
      <li><svg class="contact-icon" viewBox="0 0 16 16"><rect x="1" y="3" width="14" height="10" rx="1" fill="var(--accent-orange)"/><path d="M1 3 L8 9 L15 3" stroke="var(--card-white)" stroke-width="1.2" fill="none"/></svg>hello@brightmeadows.com</li>
      <li><svg class="contact-icon" viewBox="0 0 16 16"><circle cx="8" cy="8" r="7" fill="var(--accent-orange)"/><path d="M1 8 H15 M8 1 C4 5 4 11 8 15 M8 1 C12 5 12 11 8 15" stroke="var(--card-white)" stroke-width="1" fill="none"/></svg>www.brightmeadows.com</li>
    </ul>

    <div class="holder">
      <p><span class="holder-name">Martin Okafor</span> <span class="holder-title">| Job Title</span></p>
      <p class="holder-address">Your address Goes Here,<br>Street Name, City, Zip Code,<br>Country Name</p>
    </div>
  </section>

  <section class="card card-back" aria-label="Business card back">
    <div class="brand"><span class="brand-dot"></span>Bright Meadows</div>
    <p class="back-web">www.brightmeadows.com</p>
  </section>
</body>
</html>
```